Zelvo Stationary

Design the stationary of Zelvo Promotions Group.

Zelvo is a BTL company, BTL meaning "below the line". In other words Zelvo is a Promotional Marketing company (the company that design the brands promotional activities).

The design should transmit creativity, agility, boldness.

I need:
* Bis Card
* Letter head
* Envelopes, both vertical and horizontal (for legal size), and letter envelope
* Folders
* PPT template (Title page and regular page)
* CD slip (CD envelope)
* ID card (employee card)

And what ever else you want to throw in.
Updates

Guys,

Something I missed from the brief.   The predominat color should be RED.

Also, have fun and play with the exclamation mark (!) of the logo. 

Hi guys, more comments:

Remember that Zelvo is a "creativity" agency, not in the advertising side but on the promotional side, and that should reflect on the stationary.

 I want a bold design.  Bold and yet crisp.

 

Guys, i just uploaded the Logo in AI format.

I Also uploaded the actual Zelvo Bis Card, wich I like.  So I will like to see some designs with that bis card approach.

Guys, I am so sorry, but I notice in your last post that I upladed a wrong design ("13154_promotions_group_zelvo_brief225630.ai").  The problem was that I asked the designer the file in AI format and he send me thw wrong file, and since I dont have Illustrator I could not verify it.

The differences are minor, I just already ask him the correct one (similar to the EPS file).

Sorry                                   

Just post the correct AI file : "Zelvo Logo.ai"

Reason: I'm expecting more designs to choose from and also I wont be available tomorrow to decide.

Reason: Sorry guys, but we are not there yet!

Target Market(s)

Marketing directors, Marketing Managers

Industry/Entity Type

Legal

Requirements
Must have
• Must work with the logo attached.
The predominat color should be RED.
Play and have fun with the exclamation mark (!).
Should not have
• * No old fonts

Should not be:
* boring
* Informal
* rigid

```html
<!DOCTYPE html>
<html lang="en">
<head>
<meta charset="utf-8">
<title>Zelvo Promotions Group — Letterhead</title>
<link href="https://fonts.googleapis.com/css2?family=Montserrat:wght@700&display=swap" rel="stylesheet">
<style>
  :root {
    --paper: #ffffff;
    --ink: #111111;
    --red: #c8161d;
    --red-dark: #8a0d12;
    --red-deep: #9e1016;
    --white: #ffffff;
  }
  html, body {
    margin: 0;
    padding: 0;
    overflow: hidden;
    background: var(--paper);
  }
  .letterhead {
    position: relative;
    width: 848px;
    height: 1200px;
    overflow: hidden;
    background: var(--paper);
    font-family: "Montserrat", sans-serif;
    font-weight: 700;
  }
  .brand {
    position: absolute;
    display: flex;
    align-items: flex-start;
    gap: 8px;
    color: var(--ink);
  }
  .brand-header { left: 31px; top: 46px; }
  .brand-name {
    display: block;
    font-size: 46px;
    line-height: 40px;
    letter-spacing: -1px;
  }
  .brand-tag {
    display: block;
    margin-top: 4px;
    font-size: 9.5px;
    letter-spacing: 3.6px;
  }
  .brand-dot {
    width: 22px;
    height: 22px;
    margin-top: 26px;
    border-radius: 50%;
    background: var(--red);
  }
  .corner-panel {
    position: absolute;
    left: 0;
    top: 0;
  }
  .brand-footer {
    left: 644px;
    top: 1006px;
    color: var(--white);
  }
  .brand-footer .brand-name { font-size: 32px; line-height: 30px; }
  .brand-footer .brand-tag { font-size: 7px; letter-spacing: 2.6px; margin-top: 3px; }
  .brand-footer .brand-dot { width: 16px; height: 16px; margin-top: 18px; background: var(--white); }
  .contact {
    position: absolute;
    left: 641px;
    top: 1089px;
    color: var(--white);
    font-size: 10.5px;
    line-height: 13px;
  }
  .contact p { margin: 0; }
  .contact .line-lg { font-size: 13.5px; line-height: 17px; }
  .contact .web { font-size: 14.5px; line-height: 19px; }
</style>
</head>
<body>
<main class="letterhead">
  <div class="brand brand-header">
    <div>
      <span class="brand-name">zelvo</span>
      <span class="brand-tag">PROMOTIONS GROUP</span>
    </div>
    <span class="brand-dot"></span>
  </div>

  <svg class="corner-panel" width="848" height="1200" viewBox="0 0 848 1200" aria-hidden="true">
    <defs>
      <linearGradient id="panelFill" x1="0" y1="0" x2="1" y2="1">
        <stop offset="0" stop-color="#a7131a"/>
        <stop offset="1" stop-color="#c8161d"/>
      </linearGradient>
    </defs>
    <polygon points="629,893 848,818 848,1200 629,1200" fill="url(#panelFill)"/>
    <polygon points="629,893 848,818 848,963" fill="var(--red-dark)"/>
  </svg>

  <div class="brand brand-footer">
    <div>
      <span class="brand-name">zelvo</span>
      <span class="brand-tag">PROMOTIONS GROUP</span>
    </div>
    <span class="brand-dot"></span>
  </div>

  <address class="contact">
    <p>Calle 12 No. 45 Ens Los Pinos</p>
    <p>Santo Domingo,</p>
    <p>Republica Dominicana</p>
    <p class="line-lg">Tel: 809.555.0142</p>
    <p class="line-lg">Fax: 809.555.0178</p>
    <p class="web">www.zelvo.example.do</p>
  </address>
</main>
</body>
</html>
```